Namibia currently imports 60% of its food. Harvest Crest Oruva is an initiative which will assist Namibia to become self sustainable in terms of food production. We aim to do this through the development of 3 agricultural production zones which will include farming zones, local farmer assistance, processing and distribution of the final products. Please see our project overview attached.

```html
<!DOCTYPE html>
<html lang="en">
<head>
<meta charset="utf-8">
<title>Harvest Crest Oruva</title>
<link rel="stylesheet" href="https://fonts.googleapis.com/css2?family=Gilda+Display&family=Playfair+Display:ital@1&family=Montserrat:wght@400;500;600;700&display=swap">
<style>
:root{
  --green-deep:#0f5b2e;
  --green-bright:#4cb82a;
  --olive:#6b7d2a;
  --ink:#1e1e1e;
  --text:#333;
  --mist:#e4e9e8;
  --mint:#dcebcf;
  --teal:#0d4a49;
  --footer:#232323;
  --white:#fff;
}
*{box-sizing:border-box;margin:0;padding:0}
html,body{width:1200px;height:4448px;overflow:hidden}
body{position:relative;background:var(--white);font-family:"Montserrat",sans-serif;color:var(--text)}
.abs{position:absolute}
.serif{font-family:"Gilda Display",serif}
.accent{font-family:"Playfair Display",serif;font-style:italic;color:var(--olive)}
.photo{position:absolute}
.heading{font-family:"Gilda Display",serif;font-size:40px;color:var(--ink);font-weight:400;white-space:nowrap}
.grass{position:absolute;height:12px;background:linear-gradient(#5b6b2c,#2f3a16);border-radius:3px 3px 0 0}
.btn{position:absolute;display:flex;align-items:center;justify-content:center;gap:14px;background:var(--green-deep);color:var(--white);font-family:"Gilda Display",serif;font-size:15px;letter-spacing:1px;border-radius:3px;box-shadow:3px 3px 0 #7cbf58}
.body-copy{position:absolute;font-size:15px;line-height:25px;text-align:justify}

/* top bar */
.topbar{position:absolute;left:0;top:0;width:1200px;height:36px;background:var(--ink)}
.topbar .call-zone{position:absolute;right:0;top:0;width:420px;height:36px;background:var(--green-deep);clip-path:polygon(18px 0,100% 0,100% 100%,0 100%)}
.topbar .mail{position:absolute;left:498px;top:10px;font-size:12px;color:var(--white);display:flex;align-items:center;gap:8px}
.dot-ico{width:24px;height:24px;border-radius:50%;background:#c8a36c;display:flex;align-items:center;justify-content:center}
.topbar .phone{position:absolute;left:858px;top:5px;display:flex;align-items:center;gap:8px;color:var(--white);font-size:11px}
.topbar .phone b{font-size:19px;font-weight:700}
.brand-tab{position:absolute;left:112px;top:0;width:150px;height:150px;background:var(--white);border-radius:0 0 14px 14px;box-shadow:0 4px 10px rgba(0,0,0,.2);display:flex;flex-direction:column;align-items:center;justify-content:center;gap:6px;text-align:center}
.brand-tab .sq{width:28px;height:28px;background:var(--green-deep)}
.brand-tab span{font-family:"Gilda Display",serif;color:var(--green-deep);font-size:16px;line-height:19px}
.nav{position:absolute;top:68px;font-size:14px;color:var(--ink)}
.nav.active{color:var(--green-bright);font-weight:600}
.nav.active::after{content:"";position:absolute;left:0;right:0;top:36px;height:2px;background:var(--green-bright)}
.nav-cta{position:absolute;left:943px;top:53px;width:146px;height:47px;background:var(--green-deep);color:var(--white);font-size:13px;font-weight:700;display:flex;align-items:center;justify-content:center;gap:10px;border-radius:3px}

/* hero */
.hero-title{position:absolute;left:109px;top:236px;font-family:"Gilda Display",serif;font-size:50px;line-height:62px;color:var(--ink);letter-spacing:-.5px}
.hero-cta{position:absolute;left:109px;top:375px;width:147px;height:47px;background:var(--green-deep);color:var(--white);font-size:13px;font-weight:700;display:flex;align-items:center;justify-content:center;gap:18px;border-radius:3px}
.slide-no{position:absolute;top:648px;font-size:14px;font-weight:700;color:var(--green-bright)}

/* cards */
.card{position:absolute;top:1537px;width:299px;height:324px;background:var(--white);border:1px solid #999;border-radius:10px;overflow:hidden;box-shadow:0 3px 8px rgba(0,0,0,.15)}
.card .photo{left:0;top:0;width:100%;height:247px}
.card p{position:absolute;left:0;right:0;top:270px;text-align:center;font-family:"Gilda Display",serif;font-size:19px;color:var(--ink)}

/* form */
.field{position:absolute;background:var(--ink);color:var(--white);font-size:12px;padding:13px 18px}
.info-ico{position:absolute;width:44px;height:44px;border-radius:50%;background:var(--green-bright);display:flex;align-items:center;justify-content:center}
.info-lab{position:absolute;font-size:11px;color:#5a8a3a}
.info-val{position:absolute;font-size:14px;color:var(--ink)}

/* footer */
.footer{position:absolute;left:0;top:4066px;width:1200px;height:382px;background:var(--footer);color:var(--white)}
.foot-col{position:absolute;top:102px}
.foot-col h4{font-size:19px;font-weight:700;margin-bottom:10px}
.foot-col h4::after{content:"";display:block;width:56px;height:2px;background:#777;margin-top:10px}
.foot-col a{display:block;font-size:12px;color:#ddd;line-height:24px;text-decoration:none}
</style>
</head>
<body>

<!-- header -->
<div class="topbar">
  <div class="call-zone"></div>
  <div class="mail"><span class="dot-ico"><svg width="12" height="12" viewBox="0 0 12 12"><circle cx="6" cy="6" r="4" fill="none" stroke="#fff" stroke-width="1.4"/></svg></span>Email: info@harvestcrestoruva.com</div>
  <div class="phone"><span class="dot-ico"><svg width="12" height="12" viewBox="0 0 24 24"><path d="M6.6 10.8a15 15 0 006.6 6.6l2.2-2.2a1 1 0 011-.25 11 11 0 003.6.6 1 1 0 011 1V20a1 1 0 01-1 1A17 17 0 013 4a1 1 0 011-1h3.5a1 1 0 011 1 11 11 0 00.6 3.6 1 1 0 01-.25 1z" fill="#fff"/></svg></span>CALL US: <b>555-014-2290</b></div>
</div>
<div class="photo" role="img" aria-label="Farmer in a straw hat tending leafy green crops in a wide field under mountains" style="left:0;top:112px;width:1200px;height:604px;background:linear-gradient(180deg,#dfe3e4 0%,#c9cec6 22%,#8aa36a 45%,#5f8b3c 70%,#3f6b2a 100%)"></div>
<svg class="abs" style="left:0;top:690px" width="1200" height="30" viewBox="0 0 1200 30" aria-hidden="true"><path d="M0 18 L20 10 L40 20 L65 8 L90 19 L120 12 L150 22 L180 9 L210 18 L240 11 L270 21 L300 10 L330 19 L360 12 L390 22 L420 9 L450 18 L480 11 L510 21 L540 10 L570 20 L600 12 L630 21 L660 9 L690 19 L720 11 L750 22 L780 10 L810 19 L840 12 L870 21 L900 9 L930 18 L960 11 L990 21 L1020 10 L1050 20 L1080 12 L1110 21 L1140 9 L1170 19 L1200 12 L1200 30 L0 30Z" fill="#fff"/></svg>

<div class="brand-tab"><div class="sq"></div><span>Harvest Crest<br>Oruva</span></div>
<div class="nav active" style="left:585px">Home</div>
<div class="nav" style="left:665px">About Us</div>
<div class="nav" style="left:766px">Solutions</div>
<div class="nav" style="left:867px">Project</div>
<div class="nav-cta">CONTACT US <span>›</span></div>

<h1 class="hero-title" style="font-weight:400">AN HCO AGRI-TECH,<br>FOOD SECURITY INITIATIVE</h1>
<div class="hero-cta">CONTACT US <span>›</span></div>
<div class="slide-no" style="left:492px">01</div>
<div class="abs" style="left:515px;top:658px;width:30px;height:2px;background:var(--green-bright)"></div>
<div class="slide-no" style="left:690px">05</div>

<!-- about -->
<h2 class="heading abs" style="right:601px;top:800px">About <span class="accent">Us</span></h2>
<div class="grass" role="img" aria-label="Grass ornament" style="left:463px;top:848px;width:136px"></div>
<p class="body-copy" style="left:126px;top:890px;width:473px">Namibia is a young democracy in Sub-Saharan Africa with a population of approximately 2.5 Million people. The country's agricultural sector has been slow to keep up with the increasing population. As a consequence, approximately 60% of the food required to feed the nation is imported. The elevated cost of these imported foods means a large proportion of the population consume food with low nutritional value.</p>
<div class="btn" style="left:435px;top:1098px;width:152px;height:43px">LEARN MORE <span>›</span></div>
<div class="abs" style="left:673px;top:780px;width:380px;height:380px;border-radius:50%;background:var(--green-deep)"></div>
<div class="photo" role="img" aria-label="Smiling farmer holding a basket of fresh vegetables" style="left:687px;top:794px;width:352px;height:352px;border-radius:50%;background:radial-gradient(circle at 50% 60%,#e6c23a 0%,#8f7a4a 40%,#6a7a3a 75%,#4a5a2a 100%)"></div>

<!-- solutions -->
<div class="abs" style="left:0;top:1230px;width:1200px;height:1300px;background:var(--mist)"></div>
<svg class="abs" style="left:0;top:1230px" width="1200" height="540" viewBox="0 0 1200 540" aria-hidden="true"><path d="M0 20 Q300 0 600 12 T1200 8 L1200 522 Q900 536 600 528 T0 530Z" fill="#4cb82a"/></svg>
<h2 class="heading abs" style="left:0;width:1200px;text-align:center;top:1314px">Our <span class="accent" style="color:#1e1e1e">Solutions</span></h2>
<div class="grass" role="img" aria-label="Grass ornament" style="left:533px;top:1362px;width:134px"></div>
<p class="body-copy" style="left:109px;top:1400px;width:981px;text-align:center;font-size:15px;line-height:27px;color:#1e2e14">The long term intention of the Harvest Crest Oruva program would be to establish 3 distinct food production and processing zones which have access to large amounts of arable land, with high quality soil and strong water resources, as well as good transport connections to relevant markets. They are:</p>
<div class="card" style="left:112px"><div class="photo" role="img" aria-label="Otavi region landscape with hills, grassland and a river" style="background:linear-gradient(180deg,#8aa0b0 0%,#9a6a4a 30%,#5f7a3a 60%,#c9a24a 100%)"></div><p>Otavi Region - Central Namibia</p></div>
<div class="card" style="left:451px"><div class="photo" role="img" aria-label="Quiver tree on rocky ground under a blue sky" style="background:linear-gradient(180deg,#3d7ac0 0%,#9cbde0 45%,#b0884a 75%,#6a4a2a 100%)"></div><p>Kavango Region - North Namibia</p></div>
<div class="card" style="left:789px"><div class="photo" role="img" aria-label="Orange desert dunes beside a dry pan" style="background:linear-gradient(180deg,#c8d0d6 0%,#d98a55 40%,#c76a3a 65%,#8a7a6a 100%)"></div><p>Neckartal Dam - South Namibia</p></div>
<div class="btn" style="left:523px;top:1911px;width:150px;height:43px">LEARN MORE <span>›</span></div>

<!-- primary production -->
<div class="abs" style="left:121px;top:2300px;width:162px;height:160px;background:var(--teal);border-radius:10px"></div>
<div class="photo" role="img" aria-label="Farm worker harvesting leafy greens into crates" style="left:147px;top:2062px;width:443px;height:373px;border-radius:8px;background:linear-gradient(160deg,#4f8a30 0%,#7aa048 40%,#b0483a 55%,#4a7a2c 75%,#2f5a1e 100%)"></div>
<h2 class="heading abs" style="left:611px;top:2120px">Primary <span class="accent">Production area</span></h2>
<div class="grass" role="img" aria-label="Grass ornament" style="left:613px;top:2168px;width:136px"></div>
<p class="body-copy" style="left:613px;top:2213px;width:472px">Primary production will take place on parcels of land secured by Harvest Crest Oruva in the range of 600ha to 3,000ha. One quarter of developed land on each site will be utilised for the production of potatoes. The remainder will be used for staple food production, including maize and wheat.</p>

<!-- empowerment -->
<div class="abs" style="left:0;top:2530px;width:1200px;height:960px;background:var(--white)"></div>
<h2 class="heading abs" style="left:0;width:1200px;text-align:center;top:2608px">Empowerment <span class="accent">Production areas</span></h2>
<div class="grass" role="img" aria-label="Grass ornament" style="left:533px;top:2656px;width:134px"></div>
<p class="body-copy" style="left:111px;top:2694px;width:985px;text-align:left;font-size:14.5px">Namibia has a substantial amount of unutilised arable land in possession of either the government, or private individuals who do not have the resources or skills to develop the land into a viable food production asset. Harvest Crest Oruva aims to empower these organisations and individuals by assisting them to develop the land and operate them successfully. Support will come in the form of:</p>
<div class="abs" style="left:128px;top:2800px;width:944px;height:515px;background:var(--green-deep);border-radius:18px"></div>
<div class="photo" role="img" aria-label="Workers harvesting rows of green crops into crates" style="left:149px;top:2821px;width:902px;height:473px;border-radius:10px;background:linear-gradient(160deg,#3f7a2a 0%,#6c9a40 30%,#8a6a4a 55%,#4f8a30 75%,#6a5040 100%)"></div>
<div class="btn" style="left:523px;top:3350px;width:150px;height:43px">LEARN MORE <span>›</span></div>

<!-- contact -->
<div class="abs" style="left:0;top:3488px;width:1200px;height:580px;background:var(--mint)"></div>
<h2 class="heading abs" style="left:0;width:1200px;text-align:center;top:3588px">Contact <span class="accent">Us</span></h2>
<div class="grass" role="img" aria-label="Grass ornament" style="left:533px;top:3636px;width:134px"></div>
<p class="body-copy" style="left:109px;top:3688px;width:404px;font-size:14.5px">If you have any questions, feedback, or requests, please don't hesitate to reach out to us using the form below. Alternatively, you can contact us directly via phone or email.</p>
<div class="info-ico" style="left:126px;top:3820px"><svg width="20" height="20" viewBox="0 0 24 24"><path d="M6.6 10.8a15 15 0 006.6 6.6l2.2-2.2a1 1 0 011-.25 11 11 0 003.6.6 1 1 0 011 1V20a1 1 0 01-1 1A17 17 0 013 4a1 1 0 011-1h3.5a1 1 0 011 1 11 11 0 00.6 3.6 1 1 0 01-.25 1z" fill="#fff"/></svg></div>
<div class="info-lab" style="left:182px;top:3822px">Call Us</div>
<div class="info-val" style="left:182px;top:3838px">555-014-2290</div>
<div class="info-ico" style="left:126px;top:3890px"><svg width="20" height="16" viewBox="0 0 20 16"><rect x="1" y="1" width="18" height="14" rx="1" fill="none" stroke="#fff" stroke-width="1.8"/><path d="M1 2l9 7 9-7" fill="none" stroke="#fff" stroke-width="1.8"/></svg></div>
<div class="info-lab" style="left:182px;top:3892px">Email</div>
<div class="info-val" style="left:182px;top:3908px">info@harvestcrestoruva.com</div>
<div class="field" style="left:540px;top:3691px;width:546px;height:40px">Your Name *</div>
<div class="field" style="left:540px;top:3752px;width:263px;height:40px">Email *</div>
<div class="field" style="left:825px;top:3752px;width:261px;height:40px">Phone Number *</div>
<div class="field" style="left:540px;top:3811px;width:546px;height:126px">Enter Your Message *</div>
<div class="abs" style="left:540px;top:3945px;width:168px;height:45px;background:var(--green-bright);color:var(--white);font-size:13px;font-weight:700;display:flex;align-items:center;justify-content:center;gap:10px;border-radius:2px">SEND MESSAGE <span>›</span></div>

<!-- footer -->
<footer class="footer">
  <svg class="abs" style="left:0;top:-8px" width="1200" height="12" viewBox="0 0 1200 12" aria-hidden="true"><path d="M0 8 L30 3 L60 9 L90 2 L120 8 L150 3 L180 9 L210 2 L240 8 L270 3 L300 9 L330 2 L360 8 L390 3 L420 9 L450 2 L480 8 L510 3 L540 9 L570 2 L600 8 L630 3 L660 9 L690 2 L720 8 L750 3 L780 9 L810 2 L840 8 L870 3 L900 9 L930 2 L960 8 L990 3 L1020 9 L1050 2 L1080 8 L1110 3 L1140 9 L1170 2 L1200 8 L1200 12 L0 12Z" fill="#232323"/></svg>
  <div class="abs" style="left:254px;top:140px;width:140px;text-align:center;font-family:'Gilda Display',serif;font-size:22px;line-height:28px;color:#fff">Harvest Crest<br>Oruva</div>
  <div class="foot-col" style="left:516px"><h4>Quick Links</h4><a>Home</a><a>About Us</a><a>Solutions</a><a>Project</a><a>Contact Us</a></div>
  <div class="foot-col" style="left:703px"><h4>Links</h4><a>Copyright</a><a>Terms of Use</a><a>Privacy Policy</a><a>Accessibility</a><a>Sitemap</a></div>
  <div class="foot-col" style="left:879px"><h4>Support</h4><a>Team</a><a>About Us</a><a>Careers</a><a>Our Values</a></div>
  <div class="abs" style="left:111px;top:307px;width:978px;height:1px;background:#555"></div>
  <div class="abs" style="left:0;width:1200px;top:339px;text-align:center;font-size:13px;color:#ddd">©2024. All rights reserved.</div>
</footer>

</body>
</html>
```